"Vine Hollow Excursions" is a top notch Santa Barbara County Wine Tour company.

We provide scenic, boutique and custom wine tours. I need the card to be clean and classy. I will provide our logo. I would like the logo to cover the back side of the card as an option and would like to see a couple color options other then our signature green and gold. I would like to see some creative options and let the designers come up with options.
I need cards for myself and my team. The final design should communicate "An authentic and boutique wine tour experience"
Please use my website for reference www.vinehollowexcursions.example

Target Market(s)

We have a wide range of clients from millennials to baby boomers

Industry/Entity Type

Tour

Contact Information for Business Card

Contact info:
Dale Morton
805-219-6384
info@vinehollowexcursions.example
vinehollowexcursions.example

Colors

Designer to choose colors to be used in the design.

Requirements
Must have
• my logo
Nice to have
• *I would like to have the backside side with the logo and the company statement
• "An authentic and boutique wine tour experience" as an option.
• *I would also like to see what the designers can create!
• *I would like to see an option that incorporates or social: instagram, yelp, trip advisor
Should not have
• I do not want it too busy.

```html
<!DOCTYPE html>
<html lang="en">
<head>
<meta charset="utf-8">
<title>Vine Hollow Excursions – Business Card</title>
<link href="https://fonts.googleapis.com/css2?family=Cinzel:wght@600&family=Poppins:wght@300;400&display=swap" rel="stylesheet">
<style>
  :root {
    --canvas: #e6e6e4;
    --paper: #ffffff;
    --ink-black: #0b0b0b;
    --vine-green: #3c6b3f;
    --text-grey: #4a4a4a;
    --icon-blue: #2a7fc1;
    --icon-rose: #c7436a;
    --white: #ffffff;
  }
  * { margin: 0; padding: 0; box-sizing: border-box; }
  html, body { width: 1200px; height: 800px; overflow: hidden; }
  body {
    background: var(--canvas);
    font-family: "Poppins", sans-serif;
    display: flex;
    align-items: center;
    justify-content: center;
    gap: 48px;
  }
  .card {
    width: 540px;
    height: 309px;
    position: relative;
    box-shadow: 0 6px 18px rgba(0,0,0,0.15);
  }

  /* Front */
  .card-front { background: var(--paper); }
  .front-brand {
    position: absolute;
    top: 62px;
    right: 48px;
    display: flex;
    align-items: center;
    gap: 10px;
  }
  .brand-dot {
    width: 14px; height: 14px;
    border-radius: 50%;
    background: var(--vine-green);
  }
  .brand-name {
    font-family: "Cinzel", serif;
    font-weight: 600;
    font-size: 19px;
    letter-spacing: 1px;
    color: var(--vine-green);
  }
  .holder {
    position: absolute;
    left: 34px;
    top: 148px;
  }
  .holder-name {
    font-family: "Cinzel", serif;
    font-weight: 600;
    font-size: 22px;
    color: var(--vine-green);
    letter-spacing: 0.5px;
    line-height: 1.1;
  }
  .holder-title {
    font-size: 12px;
    color: var(--text-grey);
    letter-spacing: 1px;
    margin-top: 2px;
  }
  .divider {
    position: absolute;
    left: 34px;
    right: 34px;
    top: 200px;
    height: 1.5px;
    background: var(--vine-green);
  }
  .contacts {
    position: absolute;
    left: 34px;
    right: 20px;
    top: 214px;
    font-size: 9.6px;
    font-weight: 300;
    color: var(--text-grey);
    line-height: 2.1;
    white-space: nowrap;
  }
  .contacts .label { color: var(--vine-green); font-weight: 400; }
  .contacts .sep { color: var(--vine-green); margin: 0 4px; }
  .social-mark {
    display: inline-block;
    width: 7px; height: 7px;
    vertical-align: middle;
    margin-right: 3px;
  }
  .social-mark.blue { background: var(--icon-blue); }
  .social-mark.rose { background: var(--icon-rose); border-radius: 50%; }

  /* Back */
  .card-back { background: var(--ink-black); }
  .back-brand {
    position: absolute;
    top: 120px;
    left: 0; right: 0;
    display: flex;
    justify-content: center;
    align-items: center;
    gap: 12px;
  }
  .back-brand .brand-dot { background: var(--white); width: 16px; height: 16px; }
  .back-brand .brand-name { color: var(--white); font-size: 24px; }
  .review-link {
    position: absolute;
    left: 0; right: 0;
    top: 236px;
    text-align: center;
    color: var(--white);
    font-size: 10.5px;
    font-weight: 300;
  }
  .review-link .social-mark { background: var(--white); }
</style>
</head>
<body>

  <section class="card card-front" aria-label="Business card front">
    <div class="front-brand">
      <span class="brand-dot"></span>
      <span class="brand-name">Vine Hollow Excursions</span>
    </div>

    <div class="holder">
      <p class="holder-name">DALE MORTON</p>
      <p class="holder-title">TRIP ADVISOR</p>
    </div>

    <div class="divider"></div>

    <div class="contacts">
      <p>
        <span class="label">P :</span> 805-219-6384<span class="sep">|</span>
        <span class="label">E :</span> info@vinehollowexcursions.example<span class="sep">|</span>
        <span class="label">W :</span> www.vinehollowexcursions.example
      </p>
      <p>
        <span class="social-mark blue"></span>: /vinehollowexcursions<span class="sep">|</span>
        <span class="social-mark blue"></span>: @vinehollowexcursions<span class="sep">|</span>
        <span class="social-mark rose"></span>: @vhxwinetour
      </p>
    </div>
  </section>

  <section class="card card-back" aria-label="Business card back">
    <div class="back-brand">
      <span class="brand-dot"></span>
      <span class="brand-name">Vine Hollow Excursions</span>
    </div>
    <p class="review-link"><span class="social-mark"></span>/biz/vinehollowexcursions</p>
  </section>

</body>
</html>
```